Postcard for Real estate agent

**Scroll all the way down for updates***.....
I want a postcard to send out to potential clients to list their house on the market.
I submitting a a basic proof with the info and images that I want on each side of the postcard. I do not want a white postcard
-I want the postcard sized 6" x 4" inches
I want my phone number to stand out
I want a PLX and Homevane log on my postcard .Ive included examples of logos.
Feel free toe crop or enhance the images
Must look professional
-----------------------------------------------------------------------
UPDATE : August 4 , 2015 8pm Pacific Daylight Time , UTC -7
I submitted a proof of postcard I designed myself (see File 10)
Please use that for the front of the postcard.
For the back please refine the back to make it look professional
(see example of File 11 )
-----------------------------------------------------------------------------------------------------------
UPDATE: August 5 12:45 pm Pacific Daylight Time (UTC -7)
Please use Files 12, 13 and 14 on the front. No generic pictures.
You may crop and enhance my images if needed.
On the back, bottom of the postcard must have "If you are listed with another broker please disregard this mailing. This is not a solicitation"
UPDATE: August 5 12:45 pm Pacific Daylight Time (UTC -7)-------------------------------------------------------------------------------------Please use new Files 12, 13 and 14 on the front. No generic pictures.You may crop and enhance my images if needed.On the back, bottom of the postcard must have "If you are listed with another broker please disregard this mailing. This is not a solicitation"Upper left must have return address : 482 Corbel Rd #K Avalon CA 90815-6130 Added Wednesday, August 5, 2015
Homeowners wanting to sell their property
Real Estate Agent
- My name and phone number highly visible
- Homevane/ PLX logo
- Nothing pink, purple, lavender, brown , no pastels

```html
<!DOCTYPE html>
<html lang="en">
<head>
<meta charset="utf-8">
<title>Postcard – Maren Holloway, Harbor Cove Realtors</title>
<link rel="stylesheet" href="https://fonts.googleapis.com/css2?family=Oswald:wght@400;500;600&family=Open+Sans:ital,wght@0,400;0,600;1,400&display=swap">
<style>
  :root{
    --blue:#1f4fa6;
    --blue-deep:#16397d;
    --navy:#0f2757;
    --yellow:#f6c21a;
    --white:#ffffff;
    --paper:#f4f5f6;
    --page:#e9eaec;
    --ink:#444a52;
  }
  *{box-sizing:border-box;margin:0;padding:0}
  html,body{width:900px;height:1200px;overflow:hidden;background:var(--page)}
  body{position:relative;font-family:"Open Sans",Arial,sans-serif}
  .card{position:absolute;left:40px;width:820px;height:547px;overflow:hidden;box-shadow:0 4px 14px rgba(0,0,0,.18)}
  .card--front{top:30px;background:var(--blue)}
  .card--back{top:623px;background:var(--paper)}
  .abs{position:absolute}
  .cond{font-family:"Oswald","Arial Narrow",sans-serif;text-transform:uppercase}
  .nowrap{white-space:nowrap}

  /* front */
  .headline{left:0;top:0;width:330px;height:72px;background:var(--white);border-bottom:6px solid var(--yellow);
    display:flex;align-items:center;justify-content:center;color:var(--navy);font-size:31px;font-weight:500;letter-spacing:.5px}
  .intro{left:0;top:72px;width:330px;height:308px;background:linear-gradient(160deg,var(--blue) 0%,var(--blue-deep) 100%);
    padding:40px 20px 0 24px;border-right:6px solid var(--yellow)}
  .intro__name{color:var(--yellow);font-size:40px;font-weight:500;line-height:1.1}
  .intro__firm{color:var(--yellow);font-size:28px;font-weight:400;line-height:1.2;margin-top:2px}
  .intro__place{color:var(--white);font-size:19px;margin-top:10px}
  .call{margin-top:36px;width:280px;background:var(--white);border:3px solid var(--yellow);color:var(--blue-deep);
    font-size:20px;font-weight:600;padding:6px 0;text-align:center}
  .photo-main{left:330px;top:0;width:490px;height:380px;background:linear-gradient(180deg,#6fb0e0 0%,#c9a77e 45%,#3fb2d6 80%,#b58a62 100%)}
  .strip{left:0;top:380px;width:820px;height:167px;background:var(--yellow);display:flex;gap:5px;padding:7px}
  .tile{flex:1;height:100%}
  .tile--a{background:linear-gradient(180deg,#8ec0e6,#6f8a55 60%,#9b8b78)}
  .tile--b{background:linear-gradient(180deg,#7eb4e0,#4f6b3e 55%,#7d6a55)}
  .tile--c{background:linear-gradient(180deg,#9c7a5a,#5e7a46 60%,#c1a183)}
  .tile--d{background:linear-gradient(180deg,#8fc2ea,#4f89b6 55%,#d4b48f)}
  .tile--e{background:linear-gradient(180deg,#a9c8de,#c9a98c 60%,#6b86a6)}

  /* back */
  .info{left:0;top:0;width:330px;height:547px;background:var(--blue);border-right:6px solid var(--yellow)}
  .return{left:0;top:0;width:324px;height:108px;padding:20px 22px;color:var(--white);font-size:22px;line-height:1.35;border-bottom:5px solid var(--yellow)}
  .contact{left:0;top:113px;width:324px;height:142px;background:var(--navy)}
  .contact__name{left:22px;top:16px;color:var(--yellow);font-size:24px;font-weight:500;line-height:1.1}
  .contact__phone{left:22px;top:46px;color:var(--white);font-size:25px;line-height:1.2}
  .contact__email{left:22px;top:98px;color:var(--white);font-size:21px;line-height:1.2}
  .portrait{left:226px;top:122px;width:84px;height:84px;border-radius:50%;border:3px solid var(--white);
    background:radial-gradient(circle at 50% 40%,#e8c9a6,#9b7a5c 60%,#5b7aa3)}
  .arcade{left:0;top:268px;width:324px;height:52px;background:var(--blue-deep);border-top:3px solid var(--yellow);border-bottom:3px solid var(--yellow);
    color:var(--white);font-size:22px;font-weight:500;display:flex;align-items:center;padding-left:22px}
  .badges{left:0;top:334px;width:324px;height:64px;display:flex;align-items:center;gap:8px;padding-left:22px}
  .badge{width:36px;height:36px;background:var(--white)}
  .badge--alt{background:#d8dde6}
  .bre{color:var(--yellow);font-size:24px;margin-left:18px;font-weight:500}
  .web{left:0;top:470px;width:324px;height:77px;background:var(--blue-deep);color:var(--white);
    font-size:19px;display:flex;align-items:center;padding-left:22px;border-top:3px solid var(--yellow)}
  .stamp{left:706px;top:22px;width:88px;height:104px;border:2px dashed #9bb3cc;background:#e6ecf2}
  .notice{left:560px;top:496px;width:240px;color:var(--ink);font-size:9.5px;font-style:italic;line-height:1.35;text-align:center}
</style>
</head>
<body>

<section class="card card--front" aria-label="Postcard front">
  <div class="abs headline cond">Thinking of selling?</div>
  <div class="abs intro">
    <div class="intro__name cond nowrap">Maren Holloway</div>
    <div class="intro__firm cond nowrap">Harbor Cove Realtors</div>
    <div class="intro__place nowrap">In the post office arcade</div>
    <div class="call cond nowrap">Call me today (310) 555-0148</div>
  </div>
  <div class="abs photo-main" role="img" aria-label="Photo of a terracotta villa with a blue swimming pool and patio"></div>
  <div class="abs strip">
    <div class="tile tile--a" role="img" aria-label="Photo of a house with a garage"></div>
    <div class="tile tile--b" role="img" aria-label="Photo of a hillside home among trees"></div>
    <div class="tile tile--c" role="img" aria-label="Photo of a home with a sold sign"></div>
    <div class="tile tile--d" role="img" aria-label="Photo of the harbor with boats"></div>
    <div class="tile tile--e" role="img" aria-label="Portrait photo of the agent"></div>
  </div>
</section>

<section class="card card--back" aria-label="Postcard back">
  <div class="abs info"></div>
  <div class="abs return">482 Corbel Rd #K<br>Avalon, CA 90815-6130</div>
  <div class="abs contact">
    <div class="abs contact__name cond nowrap">Maren Holloway</div>
    <div class="abs contact__phone cond nowrap">(310) 555-0148</div>
    <div class="abs contact__email cond nowrap">sellwithmaren@mailbox.com</div>
  </div>
  <div class="abs portrait" role="img" aria-label="Round portrait photo of the agent"></div>
  <div class="abs arcade cond">In the post office arcade</div>
  <div class="abs badges">
    <span class="badge" aria-label="Homevane badge"></span>
    <span class="badge badge--alt" aria-label="PLX badge"></span>
    <span class="bre cond">BRE# 02357716</span>
  </div>
  <div class="abs web">www.HarborCoveRealtors.com</div>
  <div class="abs stamp" aria-label="Postage area"></div>
  <p class="abs notice">*If you are listed with another broker please disregard this mailing. This is not a solicitation</p>
</section>

</body>
</html>
```